Web Design for a Biotech Consulting Firm

We need a web site design for a new business based in Philadelphia called Verantel Dx. This is a consulting firm that will serve medical diagnostics industry, which is part of the life science/healthcare industry focusing on developing and marketing products that help in early detection, monitoring or management of diseases. Our consulting firm will help medical diagnostic companies to overcome key challenges in designing, evaluating and marketing new products.Our company name is Verantel Dx. Verantel is Latin word for "something" Dx represents diagnostics. The idea behind the name is that we help companies to transform the original, early product ideas ("nothing") into "something"; which is a product with full clinical utility that will help to improve health and well-being.The web site should use the visual feel of the logo (attached), be modern, simple and clean looking and represent creativity, innovation, scientific thinking and progress.
Updates

Wix Design is acceptable

Industry/Entity Type

Biotechnology

Coding

Coded - Design and coding required

Number of Pages Required

1 page

Font styles to use
Sans Serif

Requirements
Must have
• simple, clean look couple of pages
Should not have
• a lot of pages

```html
<!DOCTYPE html>
<html lang="en">
<head>
<meta charset="utf-8">
<title>Verantel Dx — Consulting for Medical Diagnostics</title>
<link rel="stylesheet" href="https://fonts.googleapis.com/css2?family=Montserrat:wght@600;700&family=Jost:wght@400;500&family=Oswald:wght@400;600;700&display=swap">
<style>
:root{
  --blue:#1b85f5;
  --blue-soft:#b5d3fb;
  --ink:#111418;
  --text:#3e4650;
  --wash:#f4f8fe;
  --foot:#f1f6fd;
  --line:#dfe6ef;
  --white:#ffffff;
}
*{box-sizing:border-box;margin:0;padding:0}
html,body{width:1200px;height:3246px;overflow:hidden}
body{position:relative;background:var(--white);font-family:'Jost',sans-serif;color:var(--text)}
.abs{position:absolute}
.wash{left:0;top:0;width:1200px;height:1204px;background:var(--wash)}
.brand-shape{left:0;top:0}
.brand-name{font-family:'Jost',sans-serif;font-weight:400;white-space:nowrap}
.logo{left:112px;top:38px;font-size:20px;color:var(--white)}
.nav{top:46px;font-family:'Montserrat',sans-serif;font-weight:700;font-size:13px;color:var(--ink)}
.nav a{position:absolute;color:inherit;text-decoration:none;white-space:nowrap}
.nav a.active{color:var(--blue)}
.hero{left:112px;top:111px;width:975px;height:517px;background:linear-gradient(90deg,#eef1f4 0%,#e3e8ee 45%,#cfd9e4 70%,#b9c9da 100%)}
.hero-kicker{left:142px;top:333px;font-family:'Oswald',sans-serif;font-weight:600;font-size:22px;color:var(--ink)}
.hero-title{left:142px;top:366px;font-family:'Oswald',sans-serif;font-weight:700;font-size:44px;color:var(--ink)}
.dot{top:458px;width:12px;height:12px;border-radius:50%;border:1.5px solid #333}
.dot.on{background:var(--blue);border-color:var(--blue)}
.about-frame{left:112px;top:718px;width:375px;height:391px;border:4px solid var(--blue-soft)}
.about-photo{left:144px;top:747px;width:374px;height:333px;background:linear-gradient(90deg,#c9cdd2,#e9ecee 50%,#d2d7dc)}
h2{font-family:'Montserrat',sans-serif;font-weight:700;font-size:30px;color:var(--ink);white-space:nowrap}
h2 span{color:var(--blue)}
.about-h{left:569px;top:764px}
.about-lead{left:569px;top:809px;width:520px;font-size:15px;line-height:23px;color:var(--ink)}
.about-body{left:569px;top:860px;width:520px;font-size:13px;line-height:23px}
.btn{display:flex;align-items:center;justify-content:center;border:2px solid var(--blue);font-family:'Oswald',sans-serif;font-size:13px;color:var(--ink)}
.about-btn{left:570px;top:1016px;width:112px;height:43px}
.services-h{left:0;width:1200px;top:1283px;text-align:center}
.card{width:304px;background:var(--white);box-shadow:0 0 8px rgba(27,133,245,.12)}
.svc{top:1351px;height:278px}
.svc .icon{position:absolute;left:18px;top:30px}
.svc h3{position:absolute;left:18px;top:106px;font-family:'Montserrat',sans-serif;font-weight:700;font-size:15px;color:var(--ink)}
.svc p{position:absolute;left:18px;top:135px;width:272px;font-size:13px;line-height:20px}
.more{position:absolute;font-family:'Oswald',sans-serif;font-size:12px;color:var(--ink);display:flex;align-items:center;gap:6px}
.svc .more{left:18px;top:236px}
.banner{left:0;top:1723px;width:1200px;height:502px;background:linear-gradient(90deg,#e8ecef 0%,#f2f4f5 35%,#dfe6ed 60%,#c7d6e4 100%)}
.banner-box{left:112px;top:1838px;width:420px;height:446px;background:var(--blue);color:var(--white);padding:55px 24px 0}
.banner-box h3{font-family:'Montserrat',sans-serif;font-weight:700;font-size:29px;line-height:39px}
.banner-box p{margin-top:16px;font-size:15px;line-height:25.5px}
.banner-box .more{left:24px;top:370px;color:var(--white)}
.news-h{left:0;width:1200px;top:2362px;text-align:center}
.news{top:2433px;height:340px;border:1px solid var(--line);box-shadow:none}
.news .photo{position:absolute;left:6px;top:6px;width:291px;height:237px}
.news .date{position:absolute;left:18px;top:264px;font-family:'Oswald',sans-serif;font-size:11px;color:var(--blue)}
.news h4{position:absolute;left:18px;top:282px;width:272px;font-family:'Montserrat',sans-serif;font-weight:700;font-size:13px;line-height:20px;color:var(--ink)}
.view-btn{left:543px;top:2806px;width:112px;height:40px}
.footer{left:0;top:2937px;width:1200px;height:309px;background:var(--foot)}
.fh{top:2993px;font-family:'Montserrat',sans-serif;font-weight:700;font-size:14px;color:var(--blue)}
.links{left:113px;top:3022px;list-style:none;font-size:13px;color:var(--ink)}
.links li{height:27.2px;display:flex;align-items:center;gap:9px}
.links li::before{content:"»";color:#777;font-size:12px}
.contact{left:304px;top:3022px;font-size:13px;color:var(--ink);line-height:18px}
.contact .row{display:flex;gap:9px;align-items:flex-start;margin-bottom:10px}
.contact svg{flex:none;margin-top:2px}
.map{left:620px;top:3029px;width:243px;height:113px;background:linear-gradient(135deg,#efe9da,#e6e3d6 50%,#dfe3d8)}
.foot-logo{left:958px;top:3064px;font-size:24px;color:var(--ink)}
.rule{left:113px;top:3206px;width:974px;height:1px;background:var(--line)}
.copy{left:113px;top:3217px;font-size:12px;color:var(--ink)}
.social{top:3215px;width:23px;height:23px}
</style>
</head>
<body>
<div class="abs wash"></div>
<svg class="abs brand-shape" width="580" height="781" viewBox="0 0 580 781" aria-hidden="true">
  <polygon fill="#1b85f5" points="0,0 580,0 498,111 112,111 112,630 0,781"/>
</svg>
<div class="abs brand-name logo">Verantel Dx</div>

<nav class="abs nav" style="left:0">
  <a class="active" style="left:629px">HOME</a>
  <a style="left:711px">ABOUT US</a>
  <a style="left:819px">SERVIES</a>
  <a style="left:918px">NEWS</a>
  <a style="left:1002px">CONTACT US</a>
</nav>

<section>
  <div class="abs hero" role="img" aria-label="Smiling lab scientist in safety glasses and blue gloves holding a pipette over a rack of test tubes"></div>
  <div class="abs hero-kicker">CONSULTING FIRM SERVING MEDICAL</div>
  <div class="abs hero-title">DIAGNOSTICS INDUSTRY</div>
  <span class="abs dot" style="left:143px"></span>
  <span class="abs dot on" style="left:160px"></span>
  <span class="abs dot" style="left:178px"></span>
</section>

<section>
  <div class="abs about-frame"></div>
  <div class="abs about-photo" role="img" aria-label="Businessman shaking hands with a scientist in a lab coat in a laboratory corridor"></div>
  <h2 class="abs about-h">ABOUT <span>VERANTEL DX</span></h2>
  <p class="abs about-lead">Lorem ipsum dolor sit amet, consectetuer adipiscing elit, sed diam nonummy nibh euismod tincidunt ut laoreet dolore magna.</p>
  <p class="abs about-body">Lorem ipsum dolor sit amet, consectetuer adipiscing elit, sed diam nonummy nibh mod tincidunt ut laoreet dolore magna aliquam erat volutpat. Ut wisi enim ad minim venim, quis nostrud exerci tation ullaorper suscpit lobortis nisl ut aliquip ex ea comodo consat. Duis autem vel eum iriure dolor in hendrerit in vulputate velit esse molestie consequat, vel illum dolore eu feugiat nulla facilisis at vero eros et accumsan et iusto odio dignissim qui blandit praesent luptatum zzril delenit augue duis facilisi.</p>
  <div class="abs btn about-btn">READ MORE</div>
</section>

<section>
  <h2 class="abs services-h">OUR <span>SERVICES</span></h2>

  <article class="abs card svc" style="left:112px">
    <svg class="icon" width="62" height="62" viewBox="0 0 62 62" fill="none" stroke="#1b85f5" stroke-width="2">
      <rect x="2" y="4" width="58" height="40" rx="2"/><line x1="2" y1="36" x2="60" y2="36"/>
      <path d="M24 44v8M38 44v8M18 54h26"/><path d="M14 30V16l4-6 4 6v14z"/><path d="M30 30V12M26 30h8M44 30V14h6v16z"/>
    </svg>
    <h3>DESIGNING</h3>
    <p>Lorem ipsum dolor sit consectetuer adipiscing elit sed diam nonumy nibh euismod tincidunt ut laoreet dolore magna.Ut wisi enim minim venim quis nostrud exerci.</p>
    <div class="more">READ MORE <svg width="16" height="8" viewBox="0 0 16 8"><path d="M0 4h14M10 1l4 3-4 3" stroke="#111" stroke-width="1.6" fill="none"/></svg></div>
  </article>

  <article class="abs card svc" style="left:447px">
    <svg class="icon" width="62" height="62" viewBox="0 0 62 62" fill="none" stroke="#1b85f5" stroke-width="2">
      <rect x="4" y="4" width="40" height="54" rx="2"/><rect x="16" y="1" width="16" height="7"/>
      <rect x="11" y="16" width="7" height="7"/><rect x="11" y="29" width="7" height="7"/><rect x="11" y="42" width="7" height="7"/>
      <path d="M22 19h12M22 32h12M22 45h8M12 19l3 3 5-6"/><path d="M46 20l8 4-14 26-6 2 0-6z"/>
    </svg>
    <h3>EVALUATING</h3>
    <p>Lorem ipsum dolor sit consectetuer adipiscing elit sed diam nonumy nibh euismod tincidunt ut laoreet dolore magna.Ut wisi enim minim venim quis nostrud exerci.</p>
    <div class="more">READ MORE <svg width="16" height="8" viewBox="0 0 16 8"><path d="M0 4h14M10 1l4 3-4 3" stroke="#111" stroke-width="1.6" fill="none"/></svg></div>
  </article>

  <article class="abs card svc" style="left:783px">
    <svg class="icon" width="62" height="62" viewBox="0 0 62 62" fill="none" stroke="#1b85f5" stroke-width="2">
      <path d="M6 38l26-24 10 22-32 8z"/><path d="M10 44l6 12 6-3-4-10"/><path d="M4 36l4 10"/>
      <path d="M44 14l6-6M48 22h8M40 8V2"/>
    </svg>
    <h3>MARKETING</h3>
    <p>Lorem ipsum dolor sit consectetuer adipiscing elit sed diam nonumy nibh euismod tincidunt ut laoreet dolore magna.Ut wisi enim minim venim quis nostrud exerci.</p>
    <div class="more">READ MORE <svg width="16" height="8" viewBox="0 0 16 8"><path d="M0 4h14M10 1l4 3-4 3" stroke="#111" stroke-width="1.6" fill="none"/></svg></div>
  </article>
</section>

<section>
  <div class="abs banner" role="img" aria-label="Scientist in safety goggles pouring liquid into coloured test tubes in a bright laboratory"></div>
  <div class="abs banner-box">
    <h3>UT WISI ENIM AD MINIM VENIM, QUIS NOSTRUD EXERCI TATION</h3>
    <p>Lorem ipsum dolor sit amet, consectetuer adipiscing elit, sed diam nonummy nibh mod tincidunt ut laoreet dolore magna aliquam erat volutpat. Ut wisi enim ad minim venim, quis nostrud exerci tation ullaorper suscpit lobortis nisl ut aliquip ex ea comodo consat. Duis autem vel eum iriure dolor in hendrerit.</p>
    <div class="more">LEARN MORE <svg width="16" height="8" viewBox="0 0 16 8"><path d="M0 4h14M10 1l4 3-4 3" stroke="#fff" stroke-width="1.6" fill="none"/></svg></div>
  </div>
</section>

<section>
  <h2 class="abs news-h">LATEST <span>NEWS</span></h2>
  <article class="abs card news" style="left:112px">
    <div class="photo" role="img" aria-label="Gloved hand pipetting blue liquid into laboratory flasks" style="background:linear-gradient(135deg,#2f6f9a,#5fa8c8 55%,#2b5d82)"></div>
    <div class="date">June 15, 2019</div>
    <h4>Lorem ipsum dolor sit a consectetuer adipiscing elit sed diam</h4>
  </article>
  <article class="abs card news" style="left:447px">
    <div class="photo" role="img" aria-label="Researcher reviewing data at a computer in a laboratory" style="background:linear-gradient(135deg,#5a6f80,#c9d4dc 55%,#8fa2b2)"></div>
    <div class="date">June 15, 2019</div>
    <h4>Lorem ipsum dolor sit a consectetuer adipiscing elit sed diam</h4>
  </article>
  <article class="abs card news" style="left:783px">
    <div class="photo" role="img" aria-label="Pipette over test tubes with a molecular structure overlay" style="background:linear-gradient(135deg,#2e7fb8,#7cc4e6 50%,#1f5f96)"></div>
    <div class="date">June 15, 2019</div>
    <h4>Lorem ipsum dolor sit a consectetuer adipiscing elit sed diam</h4>
  </article>
  <div class="abs btn view-btn">VIEW ALL</div>
</section>

<footer>
  <div class="abs footer"></div>
  <div class="abs fh" style="left:113px">QUICK LINKS</div>
  <div class="abs fh" style="left:304px">CONTACT DETAILS</div>
  <div class="abs fh" style="left:618px">LOCATION MAP</div>
  <ul class="abs links">
    <li>Home</li><li>About us</li><li>Services</li><li>News</li><li>Contact Us</li>
  </ul>
  <div class="abs contact">
    <div class="row">
      <svg width="11" height="15" viewBox="0 0 11 15"><path d="M5.5 0A5.5 5.5 0 0 0 0 5.5C0 9.5 5.5 15 5.5 15S11 9.5 11 5.5A5.5 5.5 0 0 0 5.5 0zm0 8A2.5 2.5 0 1 1 5.5 3a2.5 2.5 0 0 1 0 5z" fill="#1b85f5"/></svg>
      <div><b style="font-weight:500">VERANTEL DX</b><br>123 Lorem ipsum dolor sit amet,<br>consectetuer adipiscing elit.</div>
    </div>
    <div class="row">
      <svg width="13" height="13" viewBox="0 0 13 13"><path d="M3 0l2.5 3-1.5 2a8 8 0 0 0 4 4l2-1.5L13 10l-1.5 2.5C6 13 0 7 .5 1.5z" fill="#1b85f5"/></svg>
      <div>(215) 555-0142</div>
    </div>
    <div class="row">
      <svg width="15" height="13" viewBox="0 0 15 13" fill="none" stroke="#1b85f5" stroke-width="1.4"><rect x="1" y="2" width="13" height="9"/><path d="M1 2l6.5 5L14 2"/></svg>
      <div>info@veranteldx.com</div>
    </div>
  </div>
  <div class="abs map" role="img" aria-label="Street map of the office location"></div>
  <div class="abs brand-name foot-logo">Verantel Dx</div>
  <div class="abs rule"></div>
  <div class="abs copy">Copyright © 2019 VERANTEL DX. All Rights Reserved.</div>
  <div class="abs social" style="left:974px;background:#3b5998" aria-label="Social link"></div>
  <div class="abs social" style="left:1005px;background:#1da1f2" aria-label="Social link"></div>
  <div class="abs social" style="left:1035px;background:#0e76a8" aria-label="Social link"></div>
  <div class="abs social" style="left:1065px;background:#a0785a" aria-label="Social link"></div>
</footer>
</body>
</html>
```